website design Investment Fund

I am looking for a custom website that will work on desktop computer, tablet device and a cellular device. I have attached the booklet so you can get an idea of the look we are going for. Would like to use the website eventually for crowdfunding. We like the ski racer and mountain climbing designs.

Target Market(s)

Financial Services

Industry/Entity Type

Financial Service

Coding

Coded - Design and coding required

Number of Pages Required

5+ page

Font styles to use
Sans Serif

Requirements
Must have
• Must be viewable on a cell phone and tablet and desktop
Nice to have
• Contact us form

```html
<!DOCTYPE html>
<html lang="en">
<head>
<meta charset="utf-8">
<title>Ridgeline Capital II</title>
<link href="https://fonts.googleapis.com/css2?family=Montserrat:wght@500;600;700&family=Open+Sans:wght@400;600;700&display=swap" rel="stylesheet">
<style>
:root{
  --navy:#1b3f8f;
  --red:#e30613;
  --ink:#222831;
  --text:#555b63;
  --band:#2d3646;
  --band-dark:#1f2530;
  --white:#ffffff;
  --field:#d9d9d9;
}
*{margin:0;padding:0;box-sizing:border-box}
html,body{width:1200px;height:4145px;overflow:hidden}
body{position:relative;background:var(--white);font-family:"Open Sans",sans-serif;color:var(--ink)}
.abs{position:absolute}
.heading{font-family:"Montserrat",sans-serif;font-weight:600;text-transform:uppercase;color:var(--ink);text-align:center}

/* header */
.site-header{left:0;top:0;width:1200px;height:100px;background:var(--white)}
.brand{left:110px;top:56px;font-family:"Open Sans",sans-serif}
.brand-name{font-size:19px;font-weight:700;color:var(--navy);display:flex;align-items:center;gap:8px}
.brand-name i{display:inline-block;width:14px;height:14px;background:var(--navy)}
.brand-tag{font-size:11px;font-weight:700;color:var(--red);margin-left:22px;letter-spacing:.3px}
.contact-chip{display:flex;align-items:center;gap:14px}
.chip-icon{width:34px;height:34px;border-radius:50%;background:var(--red);display:flex;align-items:center;justify-content:center}
.chip-small{font-size:12px;color:var(--ink)}
.chip-big{font-size:17px;font-weight:700;color:var(--ink)}
.main-nav{left:368px;top:66px;display:flex;gap:22px;font-size:14px;font-weight:600;color:var(--ink)}
.main-nav .active{color:var(--navy);position:relative}
.main-nav .active:after{content:"";position:absolute;left:50%;top:24px;margin-left:-6px;border:6px solid transparent;border-bottom:9px solid var(--navy);border-top:0}
.nav-cta{left:945px;top:58px;width:142px;height:38px;background:var(--navy);color:var(--white);font-size:14px;font-weight:600;display:flex;align-items:center;justify-content:center;gap:8px}

/* hero */
.hero{left:0;top:100px;width:1200px;height:624px}
.hero-photo{position:absolute;inset:0;background:linear-gradient(180deg,#1b3a6e 0%,#4c6f9c 35%,#c9d6e3 60%,#8a8f96 100%)}
.hero-title{left:0;top:168px;width:1200px;font-family:"Montserrat",sans-serif;font-weight:500;font-size:48px;color:var(--white);text-align:center}
.hero-sub{left:0;top:238px;width:1200px;font-size:19px;line-height:34px;color:var(--white);text-align:center}
.btn{display:flex;align-items:center;background:var(--navy);color:var(--white);font-family:"Open Sans",sans-serif;font-weight:700;font-size:14px;text-transform:uppercase;height:50px}
.btn .mark{width:36px;height:50px;background:var(--red);margin-right:18px}
.hero-btn{left:495px;top:339px;width:187px}
.dots{left:566px;top:587px;display:flex;gap:4px}
.dots span{width:11px;height:11px;border:2px solid var(--white);border-radius:50%}
.dots span:first-child{background:var(--white)}

/* about */
.about-photo{left:111px;top:828px;width:392px;height:262px;background:linear-gradient(135deg,#6f9ed6 0%,#dbe7f2 45%,#9aa7b7 100%)}
.about-title{left:600px;top:800px;font-family:"Montserrat",sans-serif;font-weight:600;font-size:38px;color:var(--ink)}
.about-copy{left:600px;top:872px;width:489px;font-size:14px;line-height:28px;color:var(--text);text-align:justify}
.about-btn{left:600px;top:1104px;width:154px;height:46px}
.about-btn .mark{height:46px}

/* bands */
.band{left:0;width:1200px}
.section-title-light{font-family:"Montserrat",sans-serif;font-weight:600;font-size:38px;color:var(--white);text-transform:uppercase;text-align:center;width:1200px;left:0}
.service{width:230px;text-align:center;color:var(--white);font-size:18px;font-weight:600}
.service-ring{width:110px;height:110px;border-radius:50%;border:3px solid var(--white);margin:0 auto 18px;display:flex;align-items:center;justify-content:center}

/* investors */
.invest-card{top:1947px;width:396px;height:417px;background:var(--white);box-shadow:0 1px 6px rgba(0,0,0,.25);text-align:center}
.invest-photo{height:254px;position:relative}
.invest-tag{position:absolute;left:75px;bottom:0;width:310px;height:32px;background:var(--red);color:var(--white);font-size:18px;line-height:32px}
.invest-card h3{font-family:"Open Sans",sans-serif;font-weight:600;font-size:18px;color:var(--ink);margin-top:22px}
.invest-card .rate{font-size:15px;color:var(--ink);margin-top:12px}
.invest-card .line{font-size:14px;color:var(--text);margin-top:10px}

/* team */
.member{top:2653px;width:246px;text-align:center}
.member-frame{position:relative;width:206px;height:228px;margin:0 auto;border:3px solid var(--white);border-top:none}
.member-photo{position:absolute;left:20px;top:0;width:198px;height:190px;background:linear-gradient(180deg,#c9ccd2,#7b808a)}
.member-corner{position:absolute;left:-3px;bottom:-3px;width:18px;height:18px;background:var(--red)}
.member-name{font-family:"Open Sans",sans-serif;font-weight:700;font-size:16px;color:var(--white);margin-top:20px;text-transform:uppercase}
.member-role{font-size:14px;color:#e3e6ea;margin-top:6px}
.member .btn{width:160px;height:42px;margin:16px auto 0;font-size:14px}
.member .btn .mark{height:42px;width:34px;margin-right:16px}

/* contact */
.contact-title{left:0;top:3296px;width:1200px;font-size:38px}
.form-box{left:111px;top:3359px;width:532px;height:399px;background:linear-gradient(160deg,#3a4150,#2a303a)}
.form-box h4{position:absolute;left:12px;top:30px;font-family:"Open Sans",sans-serif;font-weight:600;font-size:21px;color:var(--white)}
.field{position:absolute;height:36px;background:var(--field);font-size:14px;color:var(--text);padding:10px 20px}
.send{position:absolute;left:12px;top:335px;width:148px;height:38px;background:var(--navy);color:var(--white);font-weight:700;font-size:14px;display:flex;align-items:center;justify-content:center;text-transform:uppercase}
.map-card{left:691px;top:3359px;width:398px;height:399px;background:var(--white);box-shadow:0 1px 6px rgba(0,0,0,.2)}
.map-area{height:224px;background:linear-gradient(135deg,#eef1ee,#dfe5e2)}
.info-row{position:absolute;left:28px;display:flex;gap:18px;font-size:14px;color:var(--ink);line-height:24px}
.info-row svg{flex:none;margin-top:6px}

/* footer */
.footer{left:0;top:3827px;width:1200px;height:318px}
.footer-brand{left:0;top:3930px;width:1200px;display:flex;flex-direction:column;align-items:center;gap:10px;color:var(--white);font-weight:700;font-size:16px}
.footer-brand i{display:block;width:40px;height:40px;border-radius:50%;background:var(--red)}
.footer-nav{left:0;top:4010px;width:1200px;display:flex;justify-content:center;gap:20px;font-size:14px;color:var(--white)}
.footer-contact{left:0;top:4058px;width:1200px;display:flex;justify-content:center;align-items:center;gap:44px;font-size:14px;color:var(--white)}
.footer-contact span{display:flex;align-items:center;gap:10px}
.socials{display:flex;gap:8px}
.socials i{display:block;width:30px;height:30px;border-radius:50%;border:2px solid var(--white)}
.copyright{left:0;top:4110px;width:1200px;text-align:center;font-size:13px;color:var(--white)}
</style>
</head>
<body>

<header class="abs site-header">
  <div class="abs brand">
    <div class="brand-name"><i></i>RIDGELINE CAPITAL II</div>
    <div class="brand-tag">SECURED INCOME FUND</div>
  </div>
  <div class="abs contact-chip" style="left:596px;top:10px">
    <div class="chip-icon"><svg width="18" height="18" viewBox="0 0 24 24"><path fill="#fff" d="M6.6 10.8a15 15 0 0 0 6.6 6.6l2.2-2.2c.3-.3.7-.4 1-.2 1.1.4 2.3.6 3.6.6.6 0 1 .4 1 1V20c0 .6-.4 1-1 1A17 17 0 0 1 3 4c0-.6.4-1 1-1h3.5c.6 0 1 .4 1 1 0 1.3.2 2.5.6 3.6.1.3 0 .7-.2 1z"/></svg></div>
    <div><div class="chip-small">Call us Today</div><div class="chip-big">480-555-0142</div></div>
  </div>
  <div class="abs contact-chip" style="left:866px;top:12px">
    <div class="chip-icon"><svg width="18" height="14" viewBox="0 0 24 18"><rect x="1" y="1" width="22" height="16" fill="none" stroke="#fff" stroke-width="2"/><path d="M1 1l11 9 11-9" fill="none" stroke="#fff" stroke-width="2"/></svg></div>
    <div class="chip-big" style="font-size:15px;font-weight:600">info@ridgelinecapital.com</div>
  </div>
  <nav class="abs main-nav">
    <span class="active">Home</span><span>Aout Us</span><span>Objective</span><span>Services</span><span>Clients</span><span>Loan Programs</span><span>Folio</span>
  </nav>
  <div class="abs nav-cta"><svg width="18" height="18" viewBox="0 0 24 24"><path fill="#fff" d="M6.6 10.8a15 15 0 0 0 6.6 6.6l2.2-2.2c.3-.3.7-.4 1-.2 1.1.4 2.3.6 3.6.6.6 0 1 .4 1 1V20c0 .6-.4 1-1 1A17 17 0 0 1 3 4c0-.6.4-1 1-1h3.5c.6 0 1 .4 1 1 0 1.3.2 2.5.6 3.6.1.3 0 .7-.2 1z"/></svg>CONTACT US</div>
</header>

<section class="abs hero">
  <div class="hero-photo" role="img" aria-label="Photo of a mountaineer with trekking poles climbing a snowy alpine ridge"></div>
  <svg class="abs" style="left:0;top:0" width="1200" height="624" viewBox="0 0 1200 624">
    <polygon points="0,455 600,624 1200,455 1200,624 0,624" fill="#fff"/>
    <polyline points="0,450 600,618 1200,450" fill="none" stroke="#e30613" stroke-width="12"/>
  </svg>
  <div class="abs hero-title" style="top:68px">RIDGELINE CAPITAL</div>
  <div class="abs hero-sub" style="top:138px">Ridgeline Capital II &amp; Investment, Inc. is a privately<br>held mortgage lender, asset management</div>
  <div class="abs btn hero-btn" style="top:239px"><span class="mark"></span>GET STARTED&nbsp;&nbsp;›</div>
  <div class="abs dots" style="top:487px"><span></span><span></span><span></span><span></span><span></span></div>
</section>

<section>
  <div class="abs about-photo" role="img" aria-label="Photo of a skier carving down a slope with mountains behind"></div>
  <h2 class="abs about-title">ABOUT RIDGELINE CAPITAL</h2>
  <p class="abs about-copy">Ridgeline Capital II, Inc. is a privately held mortgage lender, asset management and advisory firm headquartered in Scottsdale, Arizona which specializes in fast financing for debt, equity, mezzanine and land bank on real estate projects in the $100,000 to $50,000,000 range. As a highly reputable, successful and growth-focused company with decades of experience across the entire spectrum of real estate financing through Arizona, the Southwest United States and Mexico.</p>
  <div class="abs btn about-btn"><span class="mark"></span>LEARN MORE</div>
</section>

<section>
  <svg class="abs band" style="top:1174px" width="1200" height="628" viewBox="0 0 1200 628" role="img" aria-label="Photo of a ski racer passing a gate on a snowy course, darkened">
    <defs><linearGradient id="svcBg" x1="0" y1="0" x2="0" y2="1"><stop offset="0" stop-color="#1e2a3d"/><stop offset="1" stop-color="#4b5566"/></linearGradient></defs>
    <polygon points="0,0 394,148 600,67 812,148 1200,0 1200,482 812,627 600,539 394,627 0,482" fill="url(#svcBg)"/>
  </svg>
  <h2 class="abs section-title-light" style="top:1360px">OUR SERVICES</h2>
  <div class="abs service" style="left:53px;top:1460px"><div class="service-ring"><svg width="56" height="56" viewBox="0 0 56 56" fill="none" stroke="#fff" stroke-width="2.5"><circle cx="20" cy="20" r="7"/><circle cx="38" cy="20" r="7"/><path d="M6 46c0-8 6-13 14-13s14 5 14 13M24 46c0-8 6-13 14-13s14 5 14 13"/></svg></div>Lending</div>
  <div class="abs service" style="left:341px;top:1460px"><div class="service-ring"><svg width="56" height="56" viewBox="0 0 56 56" fill="none" stroke="#fff" stroke-width="2.5"><path d="M14 8h22M14 48h22M16 8c0 12 18 14 18 20S16 36 16 48M34 8c0 12-18 14-18 20s18 8 18 20"/><circle cx="44" cy="38" r="7"/></svg></div>Asset Management</div>
  <div class="abs service" style="left:628px;top:1460px"><div class="service-ring"><svg width="56" height="56" viewBox="0 0 56 56" fill="none" stroke="#fff" stroke-width="2.5"><circle cx="28" cy="28" r="18" stroke-dasharray="6 3"/><rect x="20" y="24" width="16" height="12"/><path d="M18 25l10-8 10 8"/></svg></div>Real Estate Development</div>
  <div class="abs service" style="left:916px;top:1460px"><div class="service-ring"><svg width="56" height="56" viewBox="0 0 56 56" fill="none" stroke="#fff" stroke-width="2.5"><rect x="26" y="10" width="24" height="18"/><circle cx="16" cy="18" r="6"/><path d="M6 46V34c0-4 4-7 10-7s10 3 10 7v12M30 34h20v12H30z"/></svg></div>Consulting</div>
</section>

<section>
  <h2 class="abs heading" style="left:0;top:1880px;width:1200px;font-size:38px">ACCREDITED INVESTORS</h2>
  <div class="abs invest-card" style="left:174px">
    <div class="invest-photo" role="img" aria-label="Photo of a climber in red walking up a snowy ridge" style="background:linear-gradient(180deg,#3f6fae,#e6ecf2 60%,#f6f8fa)"><div class="invest-tag">Series A $50,000-$249,999</div></div>
    <h3>Minimum Investment Requirements</h3>
    <div class="rate">Rate Of Return</div>
    <div class="line">Series A 7% Per Annum</div>
    <div class="line">Term 24 Months</div>
  </div>
  <div class="abs invest-card" style="left:629px">
    <div class="invest-photo" role="img" aria-label="Photo of a ski racer in blue clearing a slalom gate" style="background:linear-gradient(180deg,#e9edf1,#c5ccd4 60%,#f2f4f6)"><div class="invest-tag">Series B $250,000.00</div></div>
    <h3>Minimum Investment Requirements</h3>
    <div class="rate">Rate Of Return</div>
    <div class="line">Series B 8% Per Annum</div>
    <div class="line">Term 24 Months</div>
  </div>
</section>

<section>
  <svg class="abs band" style="top:2407px" width="1200" height="810" viewBox="0 0 1200 810" role="img" aria-label="Photo of dark mountain peaks under an evening sky">
    <defs><linearGradient id="teamBg" x1="0" y1="0" x2="0" y2="1"><stop offset="0" stop-color="#1c2a40"/><stop offset="1" stop-color="#3d4554"/></linearGradient></defs>
    <polygon points="0,0 394,150 600,82 812,150 1200,0 1200,632 600,809 0,632" fill="url(#teamBg)"/>
  </svg>
  <h2 class="abs section-title-light" style="top:2598px">OUR TEAM</h2>
  <div class="abs member" style="left:115px">
    <div class="member-frame"><div class="member-photo" role="img" aria-label="Portrait photo of the founder and fund manager"></div><div class="member-corner"></div></div>
    <div class="member-name">Grant Holloway</div><div class="member-role">Founder and Fund Manager</div>
    <div class="btn"><span class="mark"></span>MORE INFO</div>
  </div>
  <div class="abs member" style="left:363px">
    <div class="member-frame"><div class="member-photo" role="img" aria-label="Portrait photo of the founder and managing partner"></div><div class="member-corner"></div></div>
    <div class="member-name">Diane Marsh</div><div class="member-role">Founder and Managing Partner</div>
    <div class="btn"><span class="mark"></span>MORE INFO</div>
  </div>
  <div class="abs member" style="left:609px">
    <div class="member-frame"><div class="member-photo" role="img" aria-label="Portrait photo of the fund advisor"></div><div class="member-corner"></div></div>
    <div class="member-name">Victor Hale</div><div class="member-role">Fund Advisor</div>
    <div class="btn"><span class="mark"></span>MORE INFO</div>
  </div>
  <div class="abs member" style="left:856px">
    <div class="member-frame"><div class="member-photo" role="img" aria-label="Portrait photo of the chief investment officer"></div><div class="member-corner"></div></div>
    <div class="member-name">Leo Barrington</div><div class="member-role">Chief Investment Officer</div>
    <div class="btn"><span class="mark"></span>MORE INFO</div>
  </div>
</section>

<section>
  <h2 class="abs heading contact-title">CONTACT US</h2>
  <div class="abs form-box" role="img" aria-label="Contact form over a dim mountain photo">
    <h4>GET IN TOUCH</h4>
    <div class="field" style="left:12px;top:88px;width:242px">First Name</div>
    <div class="field" style="left:278px;top:88px;width:242px">Last Name</div>
    <div class="field" style="left:12px;top:143px;width:242px">Phone Number</div>
    <div class="field" style="left:278px;top:143px;width:242px">E-Mail Address</div>
    <div class="field" style="left:12px;top:198px;width:508px;height:94px;background:rgba(217,217,217,.75)">Enter Message</div>
    <div class="send">SEND MESSAGE</div>
  </div>
  <div class="abs map-card">
    <div class="map-area" role="img" aria-label="Street map showing the office location"></div>
    <div class="info-row" style="top:245px"><svg width="12" height="14" viewBox="0 0 12 16"><path fill="#e30613" d="M6 0a6 6 0 0 0-6 6c0 4.5 6 10 6 10s6-5.5 6-10a6 6 0 0 0-6-6zm0 8.5A2.5 2.5 0 1 1 6 3.5a2.5 2.5 0 0 1 0 5z"/></svg><span>2200 N Summit Ridge Blvd,<br>Scottsdale, AZ 85260</span></div>
    <div class="info-row" style="top:315px"><svg width="12" height="12" viewBox="0 0 24 24"><path fill="#e30613" d="M6.6 10.8a15 15 0 0 0 6.6 6.6l2.2-2.2c.3-.3.7-.4 1-.2 1.1.4 2.3.6 3.6.6.6 0 1 .4 1 1V20c0 .6-.4 1-1 1A17 17 0 0 1 3 4c0-.6.4-1 1-1h3.5c.6 0 1 .4 1 1 0 1.3.2 2.5.6 3.6.1.3 0 .7-.2 1z"/></svg><span>480-555-0142</span></div>
    <div class="info-row" style="top:352px"><svg width="13" height="10" viewBox="0 0 24 18"><rect x="1" y="1" width="22" height="16" fill="none" stroke="#e30613" stroke-width="2.5"/><path d="M1 1l11 9 11-9" fill="none" stroke="#e30613" stroke-width="2.5"/></svg><span>info@ridgelinecapital.com</span></div>
  </div>
</section>

<footer>
  <svg class="abs footer" width="1200" height="318" viewBox="0 0 1200 318" role="img" aria-label="Dark silhouette of mountains and a city skyline">
    <polygon points="0,30 90,0 210,45 330,10 470,40 600,5 760,45 880,15 1010,40 1120,8 1200,30 1200,318 0,318" fill="#252c38"/>
  </svg>
  <div class="abs footer-brand"><i></i>RIDGELINE CAPITAL II</div>
  <nav class="abs footer-nav"><span>Home</span><span>|</span><span>About Us</span><span>|</span><span>Objective</span><span>|</span><span>Services</span><span>|</span><span>Clients</span><span>|</span><span>Loan Programs</span><span>|</span><span>Folio</span><span>|</span><span>Contact</span></nav>
  <div class="abs footer-contact">
    <span><svg width="14" height="11" viewBox="0 0 24 18"><rect x="1" y="1" width="22" height="16" fill="none" stroke="#fff" stroke-width="2.5"/><path d="M1 1l11 9 11-9" fill="none" stroke="#fff" stroke-width="2.5"/></svg>info@ridgelinecapital.com</span>
    <span><svg width="13" height="13" viewBox="0 0 24 24"><path fill="#fff" d="M6.6 10.8a15 15 0 0 0 6.6 6.6l2.2-2.2c.3-.3.7-.4 1-.2 1.1.4 2.3.6 3.6.6.6 0 1 .4 1 1V20c0 .6-.4 1-1 1A17 17 0 0 1 3 4c0-.6.4-1 1-1h3.5c.6 0 1 .4 1 1 0 1.3.2 2.5.6 3.6.1.3 0 .7-.2 1z"/></svg>480-555-0142</span>
    <div class="socials"><i></i><i></i><i></i><i></i></div>
  </div>
  <div class="abs copyright">© 2019 Ridgeline Capital II. All Rights Reserved</div>
</footer>

</body>
</html>
```